Geschäftspapiere für Fliesenleger - Meisterbetrieb
Zielgruppe
Wir sind ein mittelständischer Fliesenleger - Meisterbetrieb und möchten unsere Geschäftspapiere erneuern. Unsere Kunden sind Privatkunden, Gewerbetreibende sowie Öffentliche Auftraggeber.
Aufgabenstellung
Unser Logo stellen wir Ihnen zur verfügung und soll unverändert bleiben.
Wir benötigen folgende Geschäftspapiere:
- Briefpapier DIN A4
- Notizblock Karriert DIN A4
- Visitenkarten 5,5 x 8,5 cm
- Kuvert DIN lang mit Fenster
- Kuvert DIN C4 mit Fenster
Bei der Farbe Rot handelt es sich um Verkehrsrot RAL 3020
Als Schriftart haben wir uns Helvetica Neue vorgestellt.
Wir bitten jedoch auch um Vorschläge anderer Moderner und gut lesbarer Schriftarten die für Print und Web bestens geeignet sind.
Wir wünschen uns ein Modernes und Schnörkelloses Design. Bei den Dateien habe ich Ihnen ein Stockphoto angehängt um Ihnen zu zeigen wie wir uns ein Cover oder eine Broschüre vorstellen können. Nur um Ihnen unsere Ideen / Vorstellungen näher zu bringen.

```html
<!DOCTYPE html>
<html lang="de">
<head>
<meta charset="utf-8">
<title>Geschäftspapiere Fliesen-Kalder</title>
<link href="https://fonts.googleapis.com/css2?family=Inter:wght@400;500;700;800&display=swap" rel="stylesheet">
<style>
:root{
  --red:#c8201b;
  --ink:#111111;
  --paper:#ffffff;
  --window:#ebebeb;
  --grid:#e3e3e3;
  --shadow:0 1px 6px rgba(0,0,0,.14);
}
*{margin:0;padding:0;box-sizing:border-box}
html,body{width:750px;height:1200px;overflow:hidden;background:var(--paper)}
body{position:relative;font-family:"Inter",Helvetica,Arial,sans-serif;color:var(--ink)}
.sheet{position:absolute;background:var(--paper);box-shadow:var(--shadow)}
.abs{position:absolute}

/* brand name */
.brand{position:absolute;display:flex;align-items:center;gap:5px;white-space:nowrap}
.brand-name{font-weight:800;color:var(--ink);letter-spacing:-.01em;line-height:1}
.brand-square{background:var(--red);flex:none}

/* letter */
.letter{left:78px;top:41px;width:539px;height:762px}
.letter .brand{right:37px;top:78px}
.letter .brand-name{font-size:23px}
.letter .brand-square{width:10px;height:10px}
.sender-line{left:64px;top:136px;font-size:6.4px;white-space:nowrap}
.sender-line b{font-weight:700}
.recipient{left:64px;top:156px;font-size:9.4px;line-height:12px}
.fold-mark{left:0;top:270px;width:8px;height:.6px;background:var(--ink)}
.date{left:64px;top:243px;font-size:9.4px}
.subject{left:64px;top:276px;font-size:9.6px;font-weight:700}
.body-copy{left:64px;top:309px;width:384px;font-size:9.4px;line-height:11.9px}
.body-copy p{margin-bottom:11.9px}
.footer{left:64px;top:700px;font-size:6.4px;line-height:8.6px;display:flex}
.footer .col{white-space:nowrap}
.footer b{font-weight:700}
.footer .gap{height:8.6px}
.col-company{width:88px}
.col-contact{width:104px}
.col-bank{width:149px}
.contact-row{display:flex}
.contact-row b{width:10px}

/* business card */
.card{left:531px;top:220px;width:181px;height:117px}
.card .brand{left:53px;top:30px}
.card .brand-name{font-size:14px}
.card .brand-square{width:6px;height:6px}
.card-name{left:53px;top:54px;font-size:7.4px;font-weight:700}
.card-role{left:53px;top:63px;font-size:5.2px}
.card-company{left:53px;top:80px;font-size:5.2px;line-height:7.2px}
.card-company b{font-weight:700}
.card-contact{left:111px;top:80px;font-size:5.2px;line-height:7.2px}
.card-contact .contact-row b{width:8px}

/* miniatures */
.mini{position:absolute;transform-origin:0 0}
.mini-letter{left:60px;top:907px;width:539px;height:762px;transform:scale(.3228)}
.mini-card{left:202px;top:962px;width:181px;height:117px;transform:scale(.36)}
.notepad{left:285px;top:907px;width:539px;height:762px;transform:scale(.3228)}
.notepad .brand{right:37px;top:56px}
.note-line{left:34px;height:1.2px;width:166px;background:var(--grid)}
.note-grid{left:34px;top:96px;width:471px;height:608px;border:1px solid var(--grid);
  background-image:linear-gradient(var(--grid) 1px,transparent 1px),linear-gradient(90deg,var(--grid) 1px,transparent 1px);
  background-size:15.6px 15.6px}
.notepad .footer{left:0;right:37px;top:720px;justify-content:flex-end;gap:24px}

.envelope{position:absolute;background:var(--paper);box-shadow:var(--shadow)}
.env-c4{left:478px;top:886px;width:190px;height:267px}
.env-dl{left:525px;top:1025px;width:187px;height:93px}
.envelope .brand{gap:2px}
.envelope .brand-name{font-size:7.4px}
.envelope .brand-square{width:3px;height:3px}
.env-window{background:var(--window);border-radius:2px;padding:6px 8px}
.env-sender{font-size:2.2px;white-space:nowrap;margin-bottom:4px}
.env-address{font-size:3px;line-height:3.8px}
.env-web{font-size:2.6px;font-weight:700}
</style>
</head>
<body>

<!-- A4 letterhead -->
<section class="sheet letter" aria-label="Briefbogen">
  <div class="brand"><span class="brand-name">Fliesen-Kalder</span><span class="brand-square"></span></div>
  <p class="abs sender-line"><b>KHMD Kalder GmbH</b> &nbsp;·&nbsp; Unterlindach 118 &nbsp;·&nbsp; 91287 Lindenfeld</p>
  <address class="abs recipient" style="font-style:normal">Herr<br>Max Mustermann<br>Musterstraße 12<br>12345 Musterstadt</address>
  <span class="abs fold-mark"></span>
  <p class="abs date">Lindenfeld, 5. Mai 2025</p>
  <p class="abs subject">Betreff: Briefbogen</p>
  <div class="abs body-copy">
    <p>Sehr geehrter Herr Mustermann,</p>
    <p>falls Sie keine Probleme haben, diesen Blindtext schnell und zügig zu lesen, können Sie sich glücklich schätzen. Der verantwortliche Art Director, der Ihnen höchstwahrscheinlich gerade diesen Entwurf präsentiert, versteht sein typografisches Handwerk par excellence.</p>
    <p>Er hat diesen Copyblock weder gestaucht, gezerrt, noch in Versalien oder gar in 6 Punkt Quadrata Outline gesetzt. Er hat ihn ganz einfach lesbar gemacht. Offenbar sogar ziemlich gut, sonst hätten Sie wohl schon einige Zeilen zuvor die Leselust verloren. Beachten Sie nur die Zeilenbreite, die er gewählt hat. Sie ist weder zu lang noch zu kurz gewählt.</p>
    <p>Der dazugehörige Zeilenabstand ist ideal. Ihre Augen haben keinerlei Probleme, vom Ende einer Zeile in die nächste zu gelangen. Um einen solchen Art Director kann man Sie beneiden. Er nutzt den ihm gewährten gestalterischen Freiraum nicht, um sich selbst darzustellen, sondern Sie. Er weiß, daß es Wichtiges über Ihr Unternehmen oder Produkt zu sagen gibt.</p>
    <p>Und dem räumt er großzügig Platz ein. Dieser Mensch hat zweifelsohne nicht am Mäschäßutzets Inschtitut of Gräfick Ahts studiert. Er besitzt keine Bücher von Corvin Haldane oder Lisette Morwen, und wenn doch, ordnet er sie im Regal unter Kunst ein. Statt dessen pflegt er eine liebevoll innige Beziehung zu Büchern von Brandeis und Ulf Renner. Er liest sie.</p>
    <p>Mit recht freundlichen Grüßen</p>
    <p>Reinhard Kalder</p>
  </div>
  <div class="abs footer">
    <div class="col col-company"><b>KHMD Kalder GmbH</b><div class="gap"></div>Unterlindach 118<br>91287 Lindenfeld</div>
    <div class="col col-contact">
      <div class="contact-row"><b>T</b>09187 - 48 20 310</div>
      <div class="contact-row"><b>F</b>09187 - 48 20 322</div>
      <div class="contact-row"><b>M</b>post@fliesen-kalder.de</div>
      <div class="contact-row"><b>W</b>www.fliesen-kalder.de</div>
    </div>
    <div class="col col-bank"><b>Bankverbindung</b><br>Talbank Ebersfeld – Hainau<br>IBAN: DE00 0000 0000 0000 0000 00<br>BIC: TALBDEF1EBF</div>
    <div class="col"><b>Geschäftsführer</b><br>Reinhard Kalder<br>HRB 4471 Amtsgericht Lindenfeld<br>Ust. ID: DE284519907</div>
  </div>
</section>

<!-- business card -->
<section class="sheet card" aria-label="Visitenkarte">
  <div class="brand"><span class="brand-name">Fliesen-Kalder</span><span class="brand-square"></span></div>
  <p class="abs card-name">Reinhard Kalder</p>
  <p class="abs card-role">Geschäftsführer</p>
  <p class="abs card-company"><b>KHMD Kalder GmbH</b><br><br>Unterlindach 118<br>91287 Lindenfeld</p>
  <div class="abs card-contact">
    <div class="contact-row"><b>T</b>09187 - 48 20 310</div>
    <div class="contact-row"><b>F</b>09187 - 48 20 322</div>
    <div class="contact-row"><b>M</b>post@fliesen-kalder.de</div>
    <div class="contact-row"><b>W</b>www.fliesen-kalder.de</div>
  </div>
</section>

<!-- overview: letterhead -->
<section class="sheet mini mini-letter" aria-label="Briefbogen Übersicht">
  <div class="brand" style="right:37px;top:78px"><span class="brand-name" style="font-size:23px">Fliesen-Kalder</span><span class="brand-square" style="width:10px;height:10px"></span></div>
  <p class="abs sender-line"><b>KHMD Kalder GmbH</b> &nbsp;·&nbsp; Unterlindach 118 &nbsp;·&nbsp; 91287 Lindenfeld</p>
  <span class="abs fold-mark"></span>
  <div class="abs footer">
    <div class="col col-company"><b>KHMD Kalder GmbH</b><div class="gap"></div>Unterlindach 118<br>91287 Lindenfeld</div>
    <div class="col col-contact">
      <div class="contact-row"><b>T</b>09187 - 48 20 310</div>
      <div class="contact-row"><b>F</b>09187 - 48 20 322</div>
      <div class="contact-row"><b>M</b>post@fliesen-kalder.de</div>
      <div class="contact-row"><b>W</b>www.fliesen-kalder.de</div>
    </div>
    <div class="col col-bank"><b>Bankverbindung</b><br>Talbank Ebersfeld – Hainau<br>IBAN: DE00 0000 0000 0000 0000 00<br>BIC: TALBDEF1EBF</div>
    <div class="col"><b>Geschäftsführer</b><br>Reinhard Kalder<br>HRB 4471 Amtsgericht Lindenfeld<br>Ust. ID: DE284519907</div>
  </div>
</section>

<section class="sheet mini mini-card" aria-label="Visitenkarte Übersicht">
  <div class="brand" style="left:53px;top:30px"><span class="brand-name" style="font-size:14px">Fliesen-Kalder</span><span class="brand-square" style="width:6px;height:6px"></span></div>
  <p class="abs card-name">Reinhard Kalder</p>
  <p class="abs card-role">Geschäftsführer</p>
  <p class="abs card-company"><b>KHMD Kalder GmbH</b><br><br>Unterlindach 118<br>91287 Lindenfeld</p>
  <div class="abs card-contact">
    <div class="contact-row"><b>T</b>09187 - 48 20 310</div>
    <div class="contact-row"><b>F</b>09187 - 48 20 322</div>
    <div class="contact-row"><b>M</b>post@fliesen-kalder.de</div>
    <div class="contact-row"><b>W</b>www.fliesen-kalder.de</div>
  </div>
</section>

<!-- overview: squared notepad -->
<section class="sheet mini notepad" aria-label="Notizblock kariert">
  <span class="abs note-line" style="top:46px"></span>
  <span class="abs note-line" style="top:71px"></span>
  <div class="brand"><span class="brand-name" style="font-size:23px">Fliesen-Kalder</span><span class="brand-square" style="width:10px;height:10px"></span></div>
  <div class="abs note-grid"></div>
  <div class="abs footer">
    <div class="col"><b>KHMD Kalder GmbH</b></div>
    <div class="col">Unterlindach 118<br>91287 Lindenfeld</div>
    <div class="col">
      <div class="contact-row"><b>T</b>09187 - 48 20 310</div>
      <div class="contact-row"><b>F</b>09187 - 48 20 322</div>
    </div>
    <div class="col">
      <div class="contact-row"><b>M</b>post@fliesen-kalder.de</div>
      <div class="contact-row"><b>W</b>www.fliesen-kalder.de</div>
    </div>
  </div>
</section>

<!-- overview: C4 envelope -->
<section class="envelope env-c4" aria-label="Kuvert C4 mit Fenster">
  <div class="brand" style="left:43px;top:17px"><span class="brand-name">Fliesen-Kalder</span><span class="brand-square"></span></div>
  <div class="abs env-window" style="left:14px;top:45px;width:77px;height:46px">
    <p class="env-sender"><b>KHMD Kalder GmbH</b> · Unterlindach 118 · 91287 Lindenfeld</p>
    <p class="env-address">Herr<br>Max Mustermann<br>Musterstraße 12<br>12345 Musterstadt</p>
  </div>
  <p class="abs env-web" style="right:19px;top:252px">www.fliesen-kalder.de</p>
</section>

<!-- overview: DL envelope -->
<section class="envelope env-dl" aria-label="Kuvert DIN lang mit Fenster">
  <div class="brand" style="left:55px;top:10px"><span class="brand-name">Fliesen-Kalder</span><span class="brand-square"></span></div>
  <div class="abs env-window" style="left:17px;top:43px;width:77px;height:37px">
    <p class="env-sender"><b>KHMD Kalder GmbH</b> · Unterlindach 118 · 91287 Lindenfeld</p>
    <p class="env-address">Herr<br>Max Mustermann<br>Musterstraße 12<br>12345 Musterstadt</p>
  </div>
</section>

</body>
</html>
```